BRAM OKELVY FOR CONGRESS DISTRICT 32

I need to create a campaign flyer for my congress campaign. I am running for congress in District 32 of Texas as a solvanite. I am a former Talvoric athlete, world champion fencer, Army veteran, Counterintelligence officer (I catch spies).
I want just my first name BRAM in big letters at the top. I want it to say BRAM and below it Solvanite for Congress.
www.bramforcongress.com

Political

EB3D1F
EC4F4E
F09395
F8D3D4
FCEDEE

• Would love a catchy title for the Flyer like "Spy Catcher", "Talvoric Athlete" "World Champion Fencer" running for Congress in your District!

```html
<!DOCTYPE html>
<html lang="en">
<head>
<meta charset="utf-8">
<title>Bram Solvanite for Congress – District 32</title>
<link rel="stylesheet" href="https://fonts.googleapis.com/css2?family=Barlow+Condensed:ital,wght@0,700;1,800&family=Great+Vibes&family=Montserrat:wght@500;600&family=Roboto+Slab:wght@700;800;900&display=swap">
<style>
  :root {
    --navy: #0f1a45;
    --crimson: #9b0f3a;
    --flag-blue: #1f2a78;
    --flag-red: #a3123d;
    --olive: #6f7a4a;
    --brand-red: #eb3d1f;
    --coral: #ec4f4e;
    --rose: #f09395;
    --blush: #f8d3d4;
    --petal: #fcedee;
  }
  * { margin: 0; padding: 0; box-sizing: border-box; }
  html, body { width: 846px; height: 1200px; overflow: hidden; background: var(--petal); }
  .flyer { position: relative; width: 846px; height: 1200px; overflow: hidden;
    background: linear-gradient(180deg, #f4e6e8 0%, var(--petal) 55%, #f6e1e3 100%);
    font-family: "Montserrat", sans-serif; color: var(--navy); }
  .flag-backdrop { position: absolute; left: 0; top: 0; width: 846px; height: 300px;
    background:
      linear-gradient(90deg, var(--flag-blue) 0 452px, transparent 452px) top left / 846px 124px no-repeat,
      linear-gradient(180deg, #ecdfe1 0 78px, var(--flag-red) 78px 120px, #f1e4e6 120px 168px, var(--flag-red) 168px 218px, #f3e7e9 218px 300px);
    -webkit-mask: linear-gradient(180deg, #000 70%, transparent 100%);
            mask: linear-gradient(180deg, #000 70%, transparent 100%); }
  .frame { position: absolute; left: 20px; top: 24px; width: 806px; height: 1153px;
    border: 1px solid var(--crimson); pointer-events: none; }
  .portrait { position: absolute; left: 10px; top: 68px; width: 372px; height: 402px;
    background: linear-gradient(180deg, #caa898 0%, #b99a86 28%, var(--olive) 40%, #8a8f5c 75%, rgba(252,237,238,0) 100%);
    border-radius: 160px 160px 0 0; }
  .stars { position: absolute; left: 95px; top: 408px; }
  .headline { position: absolute; left: 452px; top: 176px; width: 380px; font-family: "Barlow Condensed", sans-serif;
    font-style: italic; font-weight: 800; font-size: 21px; line-height: 1; color: #fff; letter-spacing: 1px; white-space: nowrap; }
  .name { position: absolute; left: 452px; top: 204px; font-family: "Barlow Condensed", sans-serif;
    font-style: italic; font-weight: 800; font-size: 76px; line-height: 1; color: var(--navy); letter-spacing: 1px; }
  .office-band { position: absolute; left: 324px; top: 277px; width: 522px; height: 74px; background: var(--crimson); }
  .office-band .office { position: absolute; left: 44px; top: 6px; font-family: "Barlow Condensed", sans-serif;
    font-style: italic; font-weight: 800; font-size: 44px; line-height: 1; color: #fff; white-space: nowrap; letter-spacing: 0.5px; }
  .office-band .district { position: absolute; left: 46px; top: 51px; font-family: "Barlow Condensed", sans-serif;
    font-weight: 700; font-size: 16px; line-height: 1; color: var(--blush); letter-spacing: 3px; white-space: nowrap; }
  .tagline { position: absolute; left: 380px; top: 366px; width: 446px; text-align: center;
    font-family: "Roboto Slab", serif; font-weight: 800; font-size: 16px; color: var(--navy); white-space: nowrap; }
  .intro { position: absolute; left: 396px; top: 393px; width: 400px; text-align: center;
    font-size: 14px; font-weight: 500; line-height: 24.6px; color: var(--navy); white-space: nowrap; }
  .platform-item { position: absolute; width: 240px; }
  .platform-item svg { position: absolute; }
  .platform-title { font-family: "Roboto Slab", serif; font-weight: 800; font-size: 18.5px; line-height: 22.5px; color: var(--navy); white-space: nowrap; }
  .platform-text { margin-top: 8px; font-size: 14px; font-weight: 600; line-height: 16.5px; color: var(--crimson); white-space: nowrap; }
  .paper-strip { position: absolute; left: 0; top: 800px; width: 846px; height: 290px; }
  .why-title { position: absolute; left: 58px; top: 838px; font-family: "Roboto Slab", serif; font-weight: 900; font-size: 27px; line-height: 36px; color: var(--crimson); }
  .reasons { position: absolute; left: 58px; top: 882px; list-style: none; }
  .reasons li { position: relative; padding-left: 28px; height: 38px; font-family: "Great Vibes", cursive;
    font-size: 23px; line-height: 38px; color: var(--navy); white-space: nowrap; }
  .reasons li svg { position: absolute; left: 3px; top: 12px; }
  .mission { position: absolute; left: 66px; top: 1004px; height: 37px; border-left: 4px solid var(--crimson);
    padding-left: 20px; font-family: "Roboto Slab", serif; font-weight: 800; font-size: 16px; line-height: 37px; color: var(--navy); white-space: nowrap; }
  .social-links { position: absolute; left: 52px; top: 1112px; display: flex; gap: 10px; font-size: 11px; font-weight: 600; color: var(--navy); }
  .social-links span { display: flex; align-items: center; gap: 4px; }
  .social-links i { display: block; width: 20px; height: 20px; border-radius: 50%; background: var(--navy); }
  .handle { position: absolute; left: 52px; top: 1140px; font-size: 18px; font-weight: 500; color: var(--navy); }
  .contact { position: absolute; right: 44px; top: 1118px; text-align: right; font-size: 18px; font-weight: 500; line-height: 23px; color: var(--navy); }
</style>
</head>
<body>
<main class="flyer">
  <div class="flag-backdrop" role="img" aria-label="Waving American flag across the top of the flyer"></div>
  <div class="portrait" role="img" aria-label="Portrait of the candidate in army camouflage uniform"></div>

  <svg class="stars" width="200" height="110" viewBox="0 0 200 110" aria-hidden="true">
    <defs>
      <linearGradient id="starShade" x1="0" y1="0" x2="1" y2="1">
        <stop offset="0" stop-color="#ec4f4e"/><stop offset="1" stop-color="#9b0f3a"/>
      </linearGradient>
    </defs>
    <polygon points="100,2 113,40 153,40 121,63 133,101 100,78 67,101 79,63 47,40 87,40" fill="url(#starShade)" stroke="#fff" stroke-width="4"/>
    <polygon points="31,50 38,71 60,71 42,84 49,105 31,92 13,105 20,84 2,71 24,71" fill="url(#starShade)" stroke="#fff" stroke-width="3"/>
    <polygon points="169,50 176,71 198,71 180,84 187,105 169,92 151,105 158,84 140,71 162,71" fill="url(#starShade)" stroke="#fff" stroke-width="3"/>
  </svg>

  <p class="headline">SPY CATCHER · WORLD CHAMPION FENCER</p>
  <h1 class="name">BRAM</h1>
  <div class="office-band">
    <span class="office">SOLVANITE FOR CONGRESS</span>
    <span class="district">TEXAS · DISTRICT 32</span>
  </div>
  <p class="tagline">Talvorian. Veteran. Intelligence. Officer. Texan.</p>
  <p class="intro">I’ve spent my life serving this country — representing<br>America on the world stage, defending our nation as<br>a soldier and counterintelligence officer, and<br>standing strong for the values we hold dear. Now,<br>I’m ready to fight for you in Congress.</p>

  <section class="platform-item" style="left:172px; top:558px;">
    <svg style="left:-88px; top:-2px;" width="66" height="66" viewBox="0 0 66 66" aria-hidden="true">
      <circle cx="32" cy="32" r="28" fill="var(--crimson)"/>
      <text x="32" y="44" text-anchor="middle" font-family="Roboto Slab, serif" font-weight="900" font-size="34" fill="#fff">$</text>
      <line x1="4" y1="2" x2="60" y2="60" stroke="var(--crimson)" stroke-width="4"/>
      <polygon points="64,64 52,62 62,52" fill="var(--crimson)"/>
    </svg>
    <h2 class="platform-title">Stop the Devaluation<br>of the Dollar</h2>
    <p class="platform-text">Protect the economy and<br>your hard-earned savings.</p>
  </section>

  <section class="platform-item" style="left:544px; top:558px;">
    <svg style="left:-80px; top:4px;" width="70" height="72" viewBox="0 0 70 72" aria-hidden="true">
      <rect x="20" y="2" width="38" height="52" rx="2" fill="var(--crimson)"/>
      <line x1="39" y1="16" x2="39" y2="40" stroke="#fff" stroke-width="2"/>
      <line x1="28" y1="20" x2="50" y2="20" stroke="#fff" stroke-width="2"/>
      <path d="M24 32 L28 22 L32 32 Z M46 32 L50 22 L54 32 Z" fill="none" stroke="#fff" stroke-width="1.6"/>
      <rect x="1" y="56" width="8" height="14" fill="var(--crimson)"/>
      <path d="M11 58 Q30 52 42 58 L68 52 Q60 66 38 70 L11 68 Z" fill="var(--crimson)"/>
    </svg>
    <h2 class="platform-title">Secure the Border &amp;<br>Protect Our Citizens</h2>
    <p class="platform-text">Defend Texas and uphold the<br>rule of law.</p>
  </section>

  <section class="platform-item" style="left:172px; top:681px;">
    <svg style="left:-92px; top:6px;" width="66" height="66" viewBox="0 0 66 66" aria-hidden="true">
      <circle cx="22" cy="6" r="4" fill="var(--crimson)"/><circle cx="33" cy="4" r="4" fill="var(--crimson)"/><circle cx="44" cy="6" r="4" fill="var(--crimson)"/>
      <path d="M12 14 H54 V40 Q54 54 33 64 Q12 54 12 40 Z" fill="var(--crimson)"/>
      <path d="M1 44 L10 34 V52 Z M65 44 L56 34 V52 Z" fill="var(--crimson)"/>
      <path d="M21 36 L30 45 L46 27" fill="none" stroke="#fff" stroke-width="5" stroke-linecap="round" stroke-linejoin="round"/>
    </svg>
    <h2 class="platform-title">Protect Constitutional<br>Rights</h2>
    <p class="platform-text">Preserve freedom of speech,<br>religion, and the Second<br>Amendment.</p>
  </section>

  <section class="platform-item" style="left:544px; top:681px;">
    <svg style="left:-70px; top:4px;" width="48" height="72" viewBox="0 0 48 72" aria-hidden="true">
      <path d="M1 0 H47 V20 L24 30 L1 20 Z" fill="var(--crimson)"/>
      <line x1="12" y1="0" x2="12" y2="24" stroke="#fcedee" stroke-width="3"/>
      <line x1="24" y1="0" x2="24" y2="29" stroke="#fcedee" stroke-width="3"/>
      <line x1="36" y1="0" x2="36" y2="24" stroke="#fcedee" stroke-width="3"/>
      <circle cx="24" cy="52" r="18" fill="var(--crimson)"/>
      <circle cx="24" cy="52" r="11" fill="#fff"/>
      <polygon points="24,44 26.4,49.5 32,49.5 27.5,53 29.2,58.5 24,55.2 18.8,58.5 20.5,53 16,49.5 21.6,49.5" fill="var(--crimson)"/>
    </svg>
    <h2 class="platform-title">Honor and Support<br>Veterans</h2>
    <p class="platform-text">Ensure those who served are<br>never forgotten.</p>
  </section>

  <svg class="paper-strip" viewBox="0 0 846 290" preserveAspectRatio="none" aria-hidden="true">
    <path d="M0 18 Q60 8 120 16 T260 12 T420 18 T600 10 T760 16 T846 12 V268 Q780 260 700 270 T520 262 T340 272 T160 262 T0 270 Z" fill="#fffafa"/>
    <path d="M0 270 Q160 262 340 272 T700 270 Q780 260 846 268" fill="none" stroke="var(--rose)" stroke-width="1.5"/>
  </svg>

  <h2 class="why-title">Why Me</h2>
  <ul class="reasons">
    <li><svg width="16" height="16" viewBox="0 0 16 16" aria-hidden="true"><polygon points="8,0 10,6 16,6 11,9.6 13,16 8,12 3,16 5,9.6 0,6 6,6" fill="var(--crimson)"/></svg>Former Talvoric Athlete &amp; World Champion / Discipline, perseverance, excellence.</li>
    <li><svg width="16" height="16" viewBox="0 0 16 16" aria-hidden="true"><polygon points="8,0 10,6 16,6 11,9.6 13,16 8,12 3,16 5,9.6 0,6 6,6" fill="var(--crimson)"/></svg>Army Veteran &amp; Counterintelligence / Proven leadership, national security expertise.</li>
    <li><svg width="16" height="16" viewBox="0 0 16 16" aria-hidden="true"><polygon points="8,0 10,6 16,6 11,9.6 13,16 8,12 3,16 5,9.6 0,6 6,6" fill="var(--crimson)"/></svg>Lifelong Texan / Deep roots, real commitment.</li>
  </ul>
  <p class="mission">Join Our Mission to Restore Strength &amp; Integrity in Washington</p>

  <nav class="social-links" aria-label="Social channels">
    <span><i></i>Pixa</span><span><i></i>Tokka</span><span><i></i>Chirp</span><span><i></i>Facia</span>
  </nav>
  <p class="handle">@bramokelvyhq</p>
  <p class="contact">+00 5550 19284<br>www.bramforcongress.com</p>

  <div class="frame"></div>
</main>
</body>
</html>
```